Business Card Design

I am an Event and Wedding Planner in need of an eye catching business card featuring my logo (attached), my contact details, and my company tagline (Making every celebration glow with wonder...) I would like the tagline in font similar the logo's font.
Updates
I have just noticed that my logo has a misspelling so for the final design, I will be uploading a corrected logo as soon as I have it.
My apologies.
Reason: Waiting on a corrected logo...Lantern is misspelled and it should say Weddings not Wedding
The logo has been corrected so now Lantern is spelled correctly and it says Weddings instead of Wedding. Please use Edwardian Script ITC as the font for the tagline so it will match the logo. Thank you for your patience.
Target Market(s)
Engaged couples and people hosting milestone celebrations. 25-50 years old, predominately female
Industry/Entity Type
Business
Contact Information for Business Card
Rosalind Merrow, Event Manager / Owner, Mobile: 0491 868 254, Email: rosalind@velvetlanternco.com.au, www.velvetlanternco.com.au, Making every celebration glow with wonder...

```html
<!DOCTYPE html>
<html lang="en">
<head>
<meta charset="utf-8">
<title>Velvet Lantern – Business Card</title>
<link rel="stylesheet" href="https://fonts.googleapis.com/css2?family=Open+Sans:wght@400;700&family=Pinyon+Script&display=swap">
<style>
  :root {
    --bg: #e9e7e4;
    --card: #ffffff;
    --ink: #111111;
    --panel: #0b0b0b;
    --accent: #c8363c;
    --muted: #d6d6d6;
    --soft: #9a9a9a;
  }
  * { box-sizing: border-box; margin: 0; padding: 0; }
  html, body { width: 1200px; height: 800px; overflow: hidden; }
  body {
    background: var(--bg);
    font-family: "Open Sans", Arial, sans-serif;
    position: relative;
  }
  .card {
    position: absolute;
    width: 520px;
    height: 298px;
    background: var(--card);
    box-shadow: 0 4px 14px rgba(0,0,0,.18);
    overflow: hidden;
  }
  .card--front { left: 50px; top: 251px; }
  .card--back { left: 630px; top: 251px; }
  .card__shape { position: absolute; inset: 0; }
  .contact {
    position: absolute;
    left: 24px;
    top: 26px;
    color: #fff;
  }
  .contact__name {
    font-weight: 700;
    font-size: 15px;
    letter-spacing: .3px;
    text-transform: uppercase;
  }
  .contact__role { font-size: 11px; color: var(--muted); margin-top: 1px; }
  .contact__address {
    font-size: 11px;
    color: var(--muted);
    line-height: 1.55;
    margin-top: 20px;
  }
  .contact__list { list-style: none; margin-top: 24px; }
  .contact__item {
    display: flex;
    align-items: center;
    gap: 7px;
    font-size: 10.5px;
    color: var(--muted);
    line-height: 1.8;
    white-space: nowrap;
  }
  .contact__icon { width: 11px; height: 11px; flex: none; }
  .brand {
    position: absolute;
    display: flex;
    flex-direction: column;
    align-items: center;
    color: var(--ink);
    text-align: center;
  }
  .card--front .brand { left: 300px; top: 112px; width: 210px; }
  .card--back .brand { left: 0; top: 0; width: 100%; height: 100%; justify-content: center; }
  .brand__name {
    font-size: 24px;
    font-weight: 400;
    line-height: 1.1;
    display: flex;
    align-items: center;
    gap: 8px;
  }
  .brand__dot {
    width: 9px; height: 9px;
    border-radius: 50%;
    background: var(--accent);
  }
  .brand__rule {
    width: 150px;
    height: 1px;
    background: var(--soft);
    margin: 8px 0 6px;
  }
  .brand__sub { font-size: 13px; font-weight: 400; }
  .tagline {
    font-family: "Pinyon Script", cursive;
    font-size: 22px;
    color: var(--ink);
    margin-top: 22px;
  }
</style>
</head>
<body>
  <section class="card card--front" aria-label="Business card front">
    <svg class="card__shape" viewBox="0 0 520 298" aria-hidden="true">
      <path d="M0,0 H340 C270,40 238,150 272,298 H0 Z" fill="var(--accent)"/>
      <path d="M0,0 H315 C250,40 220,150 255,298 H0 Z" fill="var(--panel)"/>
    </svg>
    <div class="contact">
      <p class="contact__name">Rosalind Merrow</p>
      <p class="contact__role">Event Manager / Owner</p>
      <p class="contact__address">12 Harbour Lane, Suite 4<br>Brightwater</p>
      <ul class="contact__list">
        <li class="contact__item">
          <svg class="contact__icon" viewBox="0 0 12 12"><path d="M3 1 L5 3.5 L4 5 Q5.5 7 7 8 L8.5 7 L11 9 L9.5 11 Q5 10.5 1 3 Z" fill="var(--muted)"/></svg>
          0491 868 254
        </li>
        <li class="contact__item">
          <svg class="contact__icon" viewBox="0 0 12 12"><rect x="0.5" y="2" width="11" height="8" fill="var(--muted)"/><path d="M0.5 2 L6 6.5 L11.5 2" stroke="var(--panel)" fill="none"/></svg>
          rosalind@velvetlanternco.com.au
        </li>
        <li class="contact__item">
          <svg class="contact__icon" viewBox="0 0 12 12"><circle cx="6" cy="6" r="5" fill="none" stroke="var(--muted)"/><ellipse cx="6" cy="6" rx="2.2" ry="5" fill="none" stroke="var(--muted)"/><path d="M1 6 H11" stroke="var(--muted)"/></svg>
          www.velvetlanternco.com.au
        </li>
      </ul>
    </div>
    <div class="brand">
      <p class="brand__name">Velvet Lantern <span class="brand__dot"></span></p>
      <span class="brand__rule"></span>
      <p class="brand__sub">Weddings and Events</p>
    </div>
  </section>

  <section class="card card--back" aria-label="Business card back">
    <div class="brand">
      <p class="brand__name">Velvet Lantern <span class="brand__dot"></span></p>
      <span class="brand__rule"></span>
      <p class="brand__sub">Weddings and Events</p>
      <p class="tagline">Making every celebration glow with wonder...</p>
    </div>
  </section>
</body>
</html>
```